Birchline Septic Solutions

Would like to see some single sided ones but would also like to see some double sided with one sided only being the logo. Owners name is Colin Vandro. Phone number is 555-214-0387
Services are pumping, inspections, installs, and repairs

Contact Information for Business Card

555-241-0387 Colin Vandro Alderton, OH

```html
<!DOCTYPE html>
<html lang="en">
<head>
<meta charset="utf-8">
<title>Birchline Septic Solutions – Business Cards</title>
<link rel="stylesheet" href="https://fonts.googleapis.com/css2?family=Montserrat:wght@500;700;800&display=swap">
<style>
  :root {
    --bg: #2c2c2c;
    --card-black: #050505;
    --card-white: #ffffff;
    --teal: #2bb5ad;
    --ink: #111111;
    --ink-soft: #333333;
    --rule: #9a9a9a;
  }
  * { box-sizing: border-box; margin: 0; padding: 0; }
  html, body { width: 1200px; height: 875px; overflow: hidden; }
  body {
    background: var(--bg);
    font-family: "Montserrat", Arial, sans-serif;
    position: relative;
  }
  .card {
    position: absolute;
    width: 560px;
    height: 320px;
    border-radius: 22px;
    overflow: hidden;
    box-shadow: 0 18px 40px rgba(0,0,0,0.45);
  }
  .wordmark {
    font-weight: 800;
    text-transform: uppercase;
    letter-spacing: 0.06em;
    display: flex;
    flex-direction: column;
    white-space: nowrap;
  }

  /* Logo side */
  .card--logo {
    left: 60px; top: 110px;
    background: var(--card-black);
    display: flex; align-items: center; justify-content: center;
  }
  .card--logo .wordmark {
    color: #ffffff;
    font-size: 34px;
    line-height: 1.2;
    align-items: center;
    text-align: center;
  }

  /* Contact side */
  .card--contact {
    left: 580px; top: 445px;
    background: var(--card-white);
  }
  .contact-body {
    position: absolute; left: 0; top: 0; right: 0; height: 240px;
    display: flex; align-items: center;
    padding: 0 30px;
  }
  .card--contact .wordmark {
    color: var(--ink);
    font-size: 15px;
    line-height: 1.35;
    width: 180px;
    align-items: flex-start;
  }
  .divider {
    width: 1px; height: 110px; background: var(--rule);
    margin: 0 24px;
    flex: none;
  }
  .contact-details { white-space: nowrap; }
  .owner-name {
    color: var(--teal);
    font-weight: 800;
    font-size: 28px;
    text-transform: uppercase;
    letter-spacing: 0.01em;
    margin-bottom: 10px;
  }
  .contact-line {
    display: flex; align-items: center; gap: 10px;
    color: var(--ink);
    font-size: 19px;
    margin-top: 4px;
  }
  .contact-line--phone { font-weight: 700; }
  .contact-line--place { font-weight: 500; color: var(--ink-soft); font-size: 17px; }
  .contact-line svg { width: 18px; height: 18px; flex: none; }

  .services-band {
    position: absolute; left: 0; right: 0; bottom: 0; height: 72px;
    background: var(--card-black);
    border-top: 4px solid var(--teal);
    display: flex; align-items: center; justify-content: center;
  }
  .services {
    color: var(--teal);
    font-weight: 700;
    font-size: 18px;
    text-transform: uppercase;
    letter-spacing: 0.02em;
    white-space: nowrap;
  }
</style>
</head>
<body>

  <section class="card card--logo" aria-label="Business card, logo side">
    <div class="wordmark">
      <span>Birchline</span>
      <span>Septic Solutions</span>
    </div>
  </section>

  <section class="card card--contact" aria-label="Business card, contact side">
    <div class="contact-body">
      <div class="wordmark">
        <span>Birchline</span>
        <span>Septic Solutions</span>
      </div>
      <div class="divider"></div>
      <div class="contact-details">
        <h1 class="owner-name">Colin Vandro</h1>
        <p class="contact-line contact-line--phone">
          <svg viewBox="0 0 24 24" aria-hidden="true"><path fill="var(--teal)" d="M6.6 10.8a15.1 15.1 0 0 0 6.6 6.6l2.2-2.2a1 1 0 0 1 1-.25 11.4 11.4 0 0 0 3.6.57 1 1 0 0 1 1 1V20a1 1 0 0 1-1 1A17 17 0 0 1 3 4a1 1 0 0 1 1-1h3.5a1 1 0 0 1 1 1c0 1.25.2 2.45.57 3.57a1 1 0 0 1-.25 1z"/></svg>
          555-241-0387
        </p>
        <p class="contact-line contact-line--place">
          <svg viewBox="0 0 24 24" aria-hidden="true"><path fill="var(--teal)" d="M12 2a7 7 0 0 0-7 7c0 5.25 7 13 7 13s7-7.75 7-13a7 7 0 0 0-7-7zm0 9.5A2.5 2.5 0 1 1 12 6.5a2.5 2.5 0 0 1 0 5z"/></svg>
          Alderton, OH
        </p>
      </div>
    </div>
    <div class="services-band">
      <p class="services">Pumping, Inspections, Installs &amp; Repairs</p>
    </div>
  </section>

</body>
</html>
```